Marlow Estate Fixers (Handyman / Home Improvement Company)

Looking for a double sided professional looking business card with Logo attached to be highlighted on one side and throwing in an image of a handyman as an option would be nice to see as well. We are a company focused on providing quality Handyman and Home improvement services in a timely manner that is done right the first time with integrity

Industry/Entity Type

Handyman / Home Improvement

Contact Information for Business Card

(LOGO, Name, Mobile and office phone numbers, email) on front side of card, (the words "The SOLUTION to all of your Handyman and Home Improvement needs" followed by "Family Owned and Operated" at the very bottom) on the back.

Colors
EB3D1F
EC4F4E
F09395
F8D3D4
FCEDEE

Requirements
Must have
• Red, Gray, Black Color scheme
Should not have
• No Yellow or Blue colors

```html
<!DOCTYPE html>
<html lang="en">
<head>
<meta charset="utf-8">
<title>Marlow Estate Fixers – Business Cards</title>
<link rel="stylesheet" href="https://fonts.googleapis.com/css2?family=Montserrat:wght@400;500;700;800&display=swap">
<style>
  :root {
    --stage: #2b2b2c;
    --card: #1b1b1c;
    --card-edge: #262627;
    --red: #e8262b;
    --white: #ffffff;
    --muted: #d9d9d9;
  }
  * { box-sizing: border-box; margin: 0; padding: 0; }
  html, body { width: 1200px; height: 875px; overflow: hidden; }
  body {
    background: var(--stage);
    font-family: "Montserrat", sans-serif;
    color: var(--white);
    position: relative;
  }
  .card {
    position: absolute;
    width: 560px;
    height: 320px;
    background: var(--card);
    border: 1px solid var(--card-edge);
    border-radius: 22px;
    box-shadow: 0 18px 40px rgba(0,0,0,.55);
  }
  .card--logo { left: 50px; top: 110px; }
  .card--contact { left: 590px; top: 445px; }

  .brand {
    display: flex;
    align-items: center;
    gap: 14px;
    color: var(--red);
    font-weight: 800;
    text-transform: uppercase;
    letter-spacing: .02em;
    line-height: 1.05;
    white-space: nowrap;
  }
  .brand__mark {
    flex: none;
    border-radius: 50%;
    background: var(--red);
  }
  .card--logo .brand {
    position: absolute;
    left: 50%; top: 50%;
    transform: translate(-50%, -50%);
    font-size: 36px;
  }
  .card--logo .brand__mark { width: 60px; height: 60px; }

  .card--contact .brand {
    position: absolute;
    left: 120px; top: 48px;
    font-size: 26px;
  }
  .card--contact .brand__mark { width: 46px; height: 46px; }

  .details {
    position: absolute;
    left: 60px; top: 140px;
    display: flex;
    align-items: center;
  }
  .person { width: 210px; padding-right: 18px; text-align: right; }
  .person__name { font-size: 22px; font-weight: 700; }
  .person__name .accent { color: var(--red); }
  .person__role { font-size: 12.5px; font-weight: 500; margin-top: 2px; color: var(--muted); }
  .divider { width: 2px; height: 66px; background: var(--red); flex: none; }
  .contacts { list-style: none; padding-left: 16px; }
  .contacts li {
    display: flex; align-items: center; gap: 9px;
    font-size: 12.5px; color: var(--muted); line-height: 22px;
  }
  .contacts svg { width: 12px; height: 12px; fill: var(--red); flex: none; }
  .address {
    position: absolute;
    left: 150px; top: 235px;
    font-size: 13px;
    color: var(--muted);
    letter-spacing: .02em;
  }
</style>
</head>
<body>

<section class="card card--logo">
  <div class="brand"><span class="brand__mark"></span><span>Marlow Estate<br>Fixers</span></div>
</section>

<section class="card card--contact">
  <div class="brand"><span class="brand__mark"></span><span>Marlow Estate<br>Fixers</span></div>

  <div class="details">
    <div class="person">
      <p class="person__name">Dale <span class="accent">Hartley</span></p>
      <p class="person__role">Managing Director</p>
    </div>
    <span class="divider"></span>
    <ul class="contacts">
      <li><svg viewBox="0 0 24 24"><path d="M6.6 10.8a15.1 15.1 0 0 0 6.6 6.6l2.2-2.2a1 1 0 0 1 1-.25 11.4 11.4 0 0 0 3.6.57 1 1 0 0 1 1 1V20a1 1 0 0 1-1 1A17 17 0 0 1 3 4a1 1 0 0 1 1-1h3.5a1 1 0 0 1 1 1c0 1.25.2 2.45.57 3.6a1 1 0 0 1-.25 1z"/></svg>(08) 4410 3382</li>
      <li><svg viewBox="0 0 24 24"><path d="M2 5h20v14H2zm2 2v.5l8 5 8-5V7l-8 5z"/></svg>hello@marlowfixers.com</li>
      <li><svg viewBox="0 0 24 24"><circle cx="12" cy="12" r="10"/></svg>www.marlowfixers.com</li>
    </ul>
  </div>

  <p class="address">48 Elm Road, Marlow, USA</p>
</section>

</body>
</html>
```